Bramwell IT Services Business Card

Bramwell IT Services are a Perth based IT Services company. We would like to incorporate our company logo (attached) and stick with the blue that is in that design. I would like a clean look design that isn't too busy, yet creates a lasting image that is instantly recognisable in the recipients mind.

Target Market(s)

The target audience is small/medium business owners.

Industry/Entity Type

Business

Font styles to use
Serif
Sans Serif

Colors

Designer to choose colors to be used in the design.

Requirements
Must have
• The design should include:
Business name: Bramwell IT Services
Directors Name: Marcus Tenley
Phone Number: 0483 562 904
Email: support@bramwellit.com.au
Website: www.bramwellit.com.au

```html
<!DOCTYPE html>
<html lang="en">
<head>
<meta charset="utf-8">
<title>Bramwell IT Services – Business Card</title>
<link rel="stylesheet" href="https://fonts.googleapis.com/css2?family=Michroma&family=Oswald:wght@500;600&display=swap">
<style>
  :root {
    --backdrop: #2e2f31;
    --card-white: #ffffff;
    --blue-light: #3ec3f3;
    --blue-mid: #24a6e8;
    --blue-deep: #1a7fd6;
    --brand-navy: #1f5fb4;
    --ink-white: #ffffff;
    --dots: rgba(255, 255, 255, 0.85);
  }
  * { box-sizing: border-box; margin: 0; padding: 0; }
  html, body {
    width: 1200px;
    height: 816px;
    overflow: hidden;
    background: var(--backdrop);
  }
  .canvas {
    position: relative;
    width: 1200px;
    height: 816px;
    display: flex;
    align-items: center;
    justify-content: center;
  }
  .card {
    position: relative;
    width: 1050px;
    height: 600px;
    border-radius: 46px;
    overflow: hidden;
    background: var(--card-white);
    display: flex;
  }
  .brand-side {
    position: relative;
    width: 440px;
    height: 100%;
    display: flex;
    flex-direction: column;
    align-items: center;
    justify-content: center;
    gap: 30px;
  }
  .brand-mark {
    width: 150px;
    height: 150px;
    border-radius: 50%;
    background: linear-gradient(160deg, var(--blue-light), var(--brand-navy));
  }
  .brand-name {
    font-family: "Michroma", sans-serif;
    color: var(--brand-navy);
    text-align: center;
    line-height: 1.25;
    font-size: 38px;
    letter-spacing: 1px;
  }
  .brand-name span {
    display: block;
    font-size: 19px;
    letter-spacing: 9px;
  }
  .info-side {
    position: relative;
    flex: 1;
    height: 100%;
    background: linear-gradient(135deg, var(--blue-light) 0%, var(--blue-mid) 50%, var(--blue-deep) 100%);
    color: var(--ink-white);
    padding: 70px 60px 0 70px;
  }
  .info-side .pointer {
    position: absolute;
    left: -22px;
    bottom: 128px;
    width: 0;
    height: 0;
    border-top: 18px solid transparent;
    border-bottom: 18px solid transparent;
    border-right: 22px solid var(--blue-mid);
  }
  .contact-list {
    list-style: none;
    font-family: "Michroma", sans-serif;
    font-size: 17px;
    letter-spacing: 1.5px;
    line-height: 1.45;
  }
  .contact-item { margin-bottom: 14px; }
  .contact-item svg {
    display: block;
    width: 20px;
    height: 20px;
    margin-bottom: 4px;
    fill: var(--ink-white);
  }
  .divider {
    border: none;
    border-top: 3px dotted var(--dots);
    margin: 10px 0;
  }
  .divider.short { width: 72%; margin-left: 0; }
  .divider.long { width: 100%; }
  .person {
    text-align: right;
    font-family: "Oswald", sans-serif;
    text-transform: uppercase;
    margin-top: 18px;
  }
  .person-name {
    font-size: 52px;
    font-weight: 600;
    letter-spacing: 1px;
    line-height: 1.05;
  }
  .person-role {
    font-size: 30px;
    font-weight: 500;
    letter-spacing: 1px;
  }
</style>
</head>
<body>
<div class="canvas">
  <article class="card">
    <section class="brand-side">
      <div class="brand-mark"></div>
      <div class="brand-name">BRAMWELL<span>IT SERVICES</span></div>
    </section>
    <section class="info-side">
      <div class="pointer"></div>
      <ul class="contact-list">
        <li class="contact-item">
          <svg viewBox="0 0 24 24" aria-hidden="true"><path d="M6.6 10.8a15.1 15.1 0 0 0 6.6 6.6l2.2-2.2c.3-.3.7-.4 1-.2 1.1.4 2.3.6 3.6.6.6 0 1 .4 1 1V20c0 .6-.4 1-1 1A17 17 0 0 1 3 4c0-.6.4-1 1-1h3.5c.6 0 1 .4 1 1 0 1.3.2 2.5.6 3.6.1.3 0 .7-.2 1z"/></svg>
          0483 562 904
        </li>
        <li class="contact-item">
          <svg viewBox="0 0 24 24" aria-hidden="true"><path d="M2 5h20v14H2zm2 2v.5l8 5 8-5V7zm0 2.8V17h16V9.8l-8 5z"/></svg>
          support@bramwellit.com.au
        </li>
        <li class="contact-item">
          <svg viewBox="0 0 24 24" aria-hidden="true"><path d="M12 2a10 10 0 1 0 0 20 10 10 0 0 0 0-20zm6.9 6h-3a15 15 0 0 0-1.3-3.9A8 8 0 0 1 18.9 8zM12 4c.8 1.2 1.5 2.5 1.9 4h-3.8c.4-1.5 1.1-2.8 1.9-4zM4.3 14a8 8 0 0 1 0-4h3.4a16 16 0 0 0 0 4zm.8 2h3a15 15 0 0 0 1.3 3.9A8 8 0 0 1 5.1 16zm3-8h-3a8 8 0 0 1 4.3-3.9C8.8 5.3 8.400 6.600 8.100 8zM12 20c-.8-1.2-1.5-2.5-1.9-4h3.8c-.4 1.5-1.1 2.8-1.9 4zm2.3-6H9.7a14 14 0 0 1 0-4h4.6a14 14 0 0 1 0 4zm.3 5.9c.6-1.2 1-2.5 1.3-3.9h3a8 8 0 0 1-4.3 3.9zm1.7-5.900a16 16 0 0 0 0-4h3.4a8 8 0 0 1 0 4z"/></svg>
          www.bramwellit.com.au
        </li>
      </ul>
      <hr class="divider short">
      <ul class="contact-list">
        <li class="contact-item">
          <svg viewBox="0 0 24 24" aria-hidden="true"><path d="M12 3 2 12h3v8h5v-6h4v6h5v-8h3z"/></svg>
          418 Kelvale Street,<br>Perth WA, Australia
        </li>
      </ul>
      <hr class="divider long">
      <div class="person">
        <div class="person-name">Marcus Tenley</div>
        <div class="person-role">Director</div>
      </div>
    </section>
  </article>
</div>
</body>
</html>
```